Vexa - Booking activities for Kids and Adults.

The app allows booking of Kid's activities for a given date/time.
The app lists activities offered via various clubs (vendors) which a user can book for their kids.
The users can browse various clubs and their offered activities. The users can manage their kid's profiles.
Need a whole new look to the app. The existing app can be checked out at
https://apps.storefrontexample.test/details?id=com.vexakw
https://apps.appmarketexample.test/us/app/vexa-فيكسا/id7302958146?ls=1
Try using the app as Guest.

Target Market(s)

Kuwait

Font styles to use
Serif
Sans Serif

Requirements
Must have
• Home Screens
The home page should have everything from the existing app and a quick area to change between different kid's profile to see activities matching their interests ONLY. In the current version, there's no switch profile and hence we are showing the name tags on the activities.

We are also going to build ecommerce so we need that ecommerce look and feel.
Kindly maintain the image aspect ratio from the current app so the new version doesn't require new images.

Need a complete new innovative designs - Keep the color scheme same.
The designs should be minimalistic and image oriented. The design should be done in XD. The designs should be submitted in both light and dark theme.
Reference to be used - http://plimtor.example

D.M for more info if needed.

```html
<!DOCTYPE html>
<html lang="en">
<head>
<meta charset="utf-8">
<title>Vexa – Select Interests</title>
<link rel="stylesheet" href="https://fonts.googleapis.com/css2?family=Poppins:wght@400;500;600;700;800&display=swap">
<style>
  :root{
    --bg:#f0f3fa;
    --white:#ffffff;
    --ink:#3f3d56;
    --ink-soft:#5b5a70;
    --orange:#f7931e;
    --teal:#00d9d9;
    --pill:#e3e6ef;
    --radio:#5b5a70;
  }
  *{box-sizing:border-box;margin:0;padding:0}
  html,body{width:1200px;height:2591px;overflow:hidden}
  body{background:var(--bg);font-family:'Poppins',sans-serif;color:var(--ink);position:relative}

  .app-header{position:absolute;left:3px;top:0;width:1194px;height:327px;background:var(--white);border-radius:0 0 90px 90px}
  .back-button{position:absolute;left:62px;top:192px}
  .brand-name{position:absolute;left:0;right:0;top:140px;text-align:center;font-size:92px;font-weight:600;color:var(--orange);line-height:1}
  .cart-button{position:absolute;left:1058px;top:188px}

  .page-title{position:absolute;left:64px;top:400px;font-size:82px;font-weight:700;line-height:1.2;letter-spacing:1px}
  .profile-pill{position:absolute;left:733px;top:437px;width:194px;height:47px;border-radius:24px;background:var(--pill);font-size:26px;font-weight:600;line-height:47px;text-align:center}
  .page-intro{position:absolute;left:64px;top:510px;font-size:39px;line-height:54px;color:var(--ink-soft)}

  .interest-card{position:absolute;width:527px;height:458px;background:var(--white);border-radius:32px;border:3px solid transparent}
  .interest-card.is-selected{border-color:var(--teal)}
  .interest-art{position:absolute;left:147px;top:79px;width:210px;height:210px;border-radius:50%}
  .interest-option{position:absolute;left:58px;top:344px;display:flex;align-items:center;gap:22px;font-size:46px;font-weight:600}
  .radio{width:40px;height:40px;border-radius:50%;border:3px solid var(--radio);flex:none}
  .radio.checked{border:none;background:var(--orange);display:flex;align-items:center;justify-content:center}

  .col-a{left:61px}.col-b{left:611px}
  .row-1{top:691px}.row-2{top:1183px}.row-3{top:1673px}

  .action-button{position:absolute;top:2190px;height:89px;border-radius:45px 45px 45px 0;font-size:46px;font-weight:700;display:flex;align-items:center;justify-content:center;gap:16px}
  .skip{left:61px;width:212px;background:var(--pill);color:var(--ink-soft)}
  .next{left:879px;width:262px;background:var(--orange);color:var(--white)}

  .tab-bar{position:absolute;left:3px;top:2388px;width:1194px;height:203px;background:var(--teal);border-radius:100px 100px 0 0}
  .tab{position:absolute;top:40px;width:240px;margin-left:-120px;text-align:center;color:var(--white);font-size:30px;font-weight:700}
  .tab svg{display:block;margin:0 auto 10px}
  .tab-icon-active{width:86px;height:78px;margin:0 auto 6px;background:var(--orange);border-radius:12px;display:flex;align-items:center;justify-content:center}
</style>
</head>
<body>
  <header class="app-header">
    <svg class="back-button" width="130" height="40" viewBox="0 0 130 40" aria-label="Back and menu">
      <path d="M22 6 L10 20 L22 34" fill="none" stroke="#3f3d56" stroke-width="5" stroke-linecap="round" stroke-linejoin="round"/>
      <circle cx="60" cy="22" r="8" fill="#3f3d56"/><circle cx="87" cy="22" r="8" fill="#3f3d56"/><circle cx="114" cy="22" r="8" fill="#3f3d56"/>
    </svg>
    <div class="brand-name">Vexa</div>
    <svg class="cart-button" width="80" height="70" viewBox="0 0 80 70" aria-label="Basket, 0 items">
      <path d="M8 30 H62 L56 62 H14 Z" fill="none" stroke="#3f3d56" stroke-width="5" stroke-linejoin="round"/>
      <path d="M20 30 L35 10 L50 30" fill="none" stroke="#3f3d56" stroke-width="5" stroke-linejoin="round"/>
      <path d="M24 42 V54 M35 42 V54 M46 42 V54" stroke="#3f3d56" stroke-width="4" stroke-linecap="round"/>
      <circle cx="66" cy="14" r="12" fill="#f7931e"/>
      <text x="66" y="20" text-anchor="middle" font-family="Poppins,sans-serif" font-size="16" font-weight="700" fill="#fff">0</text>
    </svg>
  </header>

  <h1 class="page-title">Select Interests</h1>
  <div class="profile-pill">For Yousef</div>
  <p class="page-intro">This helps us suggest events and activities<br>that we thick you family will enjoy</p>

  <div class="interest-card col-a row-1">
    <div class="interest-art" role="img" aria-label="Sports equipment illustration" style="background:#f9c41a"></div>
    <div class="interest-option"><span class="radio"></span>Sports</div>
  </div>
  <div class="interest-card col-b row-1">
    <div class="interest-art" role="img" aria-label="Art easel and palette illustration" style="background:#f15a3a"></div>
    <div class="interest-option"><span class="radio"></span>Arts &amp; Crafts</div>
  </div>
  <div class="interest-card col-a row-2">
    <div class="interest-art" role="img" aria-label="Books and graduation cap illustration" style="background:#fcc74a"></div>
    <div class="interest-option"><span class="radio"></span>Education</div>
  </div>
  <div class="interest-card col-b row-2 is-selected">
    <div class="interest-art" role="img" aria-label="Dancer illustration" style="background:#7cc3ee"></div>
    <div class="interest-option"><span class="radio checked"><svg width="22" height="18" viewBox="0 0 22 18"><path d="M3 9 L9 15 L19 3" fill="none" stroke="#fff" stroke-width="4" stroke-linecap="round" stroke-linejoin="round"/></svg></span>Dance</div>
  </div>
  <div class="interest-card col-a row-3">
    <div class="interest-art" role="img" aria-label="Mixing bowl and rolling pin illustration" style="background:#8fe3f0"></div>
    <div class="interest-option"><span class="radio"></span>Cooking</div>
  </div>
  <div class="interest-card col-b row-3">
    <div class="interest-art" role="img" aria-label="Microphone illustration" style="background:#f9535d"></div>
    <div class="interest-option"><span class="radio"></span>singing</div>
  </div>

  <div class="action-button skip">Skip</div>
  <div class="action-button next">Next
    <svg width="32" height="24" viewBox="0 0 32 24"><path d="M2 12 H28 M19 4 L28 12 L19 20" fill="none" stroke="#fff" stroke-width="3" stroke-linecap="round" stroke-linejoin="round"/></svg>
  </div>

  <nav class="tab-bar">
    <div class="tab" style="left:220px;top:41px">
      <div class="tab-icon-active">
        <svg width="50" height="50" viewBox="0 0 50 50" style="margin:0"><rect x="5" y="9" width="40" height="36" rx="4" fill="none" stroke="#fff" stroke-width="3.5"/><path d="M5 19 H45 M15 4 V13 M35 4 V13" stroke="#fff" stroke-width="3.5" stroke-linecap="round"/><g fill="#fff"><rect x="12" y="25" width="5" height="5"/><rect x="22" y="25" width="5" height="5"/><rect x="32" y="25" width="5" height="5"/><rect x="12" y="34" width="5" height="5"/><rect x="22" y="34" width="5" height="5"/><rect x="32" y="34" width="5" height="5"/></g></svg>
      </div>What's On
    </div>
    <div class="tab" style="left:492px;top:52px">
      <svg width="56" height="60" viewBox="0 0 56 60"><circle cx="24" cy="26" r="17" fill="none" stroke="#fff" stroke-width="5"/><path d="M37 39 L50 52" stroke="#fff" stroke-width="6" stroke-linecap="round"/></svg>Search
    </div>
    <div class="tab" style="left:745px;top:52px">
      <svg width="50" height="60" viewBox="0 0 50 60"><path d="M8 4 H42 V56 L25 42 L8 56 Z" fill="none" stroke="#fff" stroke-width="4.5" stroke-linejoin="round"/></svg>Saved
    </div>
    <div class="tab" style="left:978px;top:52px">
      <svg width="56" height="60" viewBox="0 0 56 60"><circle cx="28" cy="18" r="14" fill="none" stroke="#fff" stroke-width="4.5"/><path d="M5 56 C6 40 16 34 28 34 C40 34 50 40 51 56" fill="none" stroke="#fff" stroke-width="4.5" stroke-linecap="round"/></svg>Account
    </div>
  </nav>
</body>
</html>
```